INTERNATIONAL SPEAKING BUSINESS FOR WOMEN NEEDS A BROCHURE DESIGN

HEARTWAYS COLLECTIVE IS AN INTERNATIONAL FEMALE NETWORK PROVIDING ITS MEMBERS THE UK'S NUMBER ONE RELATIONSHIP SEMINAR FOR WOMEN.
WE ARE ABOUT TO GO LIVE AGAIN AFTER 18 MONTHS AND ONE OF OUR OFFERINGS AT THIS LIVE EVENT, IS OUR BONDING SKILLS PROGRAMME - AND THIS IS WHERE YOU COME IN :)
IM LOOKING FOR AN ELEGANT, EASY AND WARM TO THE EYE BROCHURE WHICH CAPTURES SOME OF OUR BEST TESTIMONIALS AND CLIENTS. WE HAVE THE LOGO, THE IMAGES AND THE COPY . WE JUST NEED YOUR AMAZING CREATIVE TALENT AND SKILL TO PUT IT ALL TOGETHER TO LOOK ELEGANT AND PROFESSIONAL, YET WELCOMING AND INSPIRING.
OUR IDEAL CLIENT IS A SINGLE, SUCCESSFUL, PROFESSIONAL WOMAN WANTING TO FIND A SOLUTION TO HER RELATIONSHIP CHALLENGES. SHE WANTS TO LET GO OF HER FEARS OF PAST RELATIONSHIPS AND ALIGN WITH AN AMAZING RELATIONSHIP. OUR AIM WITH THE BROCHURE IS TO SHOW THEM WHAT WE DO, HOW WE DO IT AND HOW OUR EXISTING CLIENTS HAVE ALREADY DONE THIS.
THIS IS JUST ONE OF MANY CREATIVE WORKS NEEDED TO BE CARRIED OUT OVER THESE NEXT FEW WEEKS
SO WE ARE LOOKING FOR OUR IDEAL CREATIVE PARTNER ! HOPING TO FIND YOU HERE ;)
heartwayscollective.example
Target Market(s)
professional, successful women between 30 and 65 looking to resolve their relationship problems
Industry/Entity Type
Speaking Business/ Seminars / webinars/ Relationships Coaching for Women
Font styles to use
Other font styles liked:
- Similar to logo and website heartwayscollective.example
Look and feel

```html
<!DOCTYPE html>
<html lang="en">
<head>
<meta charset="utf-8">
<title>Heartways Collective – Bonding Skills Programme Brochure</title>
<link rel="stylesheet" href="https://fonts.googleapis.com/css2?family=Barlow+Condensed:wght@400;500;600&family=Montserrat:wght@600;700&display=swap">
<style>
  :root{
    --rose:#e23a5a;
    --rose-deep:#c7284a;
    --wine:#3a0c17;
    --charcoal:#545454;
    --charcoal-deep:#3d3d3d;
    --paper:#ffffff;
    --mist:#ececec;
    --ink:#222222;
    --stage:#f1f1f1;
  }
  *{box-sizing:border-box;margin:0;padding:0}
  html,body{width:697px;height:1200px;overflow:hidden;background:var(--stage)}
  body{font-family:"Barlow Condensed",sans-serif;color:var(--paper)}
  .spread{position:absolute;left:20px;width:657px;height:464px;display:flex;box-shadow:0 2px 10px rgba(0,0,0,.12)}
  .spread--outer{top:118px}
  .spread--inner{top:618px}
  .panel{position:relative;width:50%;height:100%;overflow:hidden}
  .abs{position:absolute}

  /* back panel */
  .panel--back{background:linear-gradient(180deg,var(--rose-deep) 0%,var(--rose) 45%,#8e1830 75%,var(--wine) 100%)}
  .crowd-photo{left:0;right:0;bottom:0;height:190px;background:linear-gradient(180deg,rgba(120,20,40,0) 0%,rgba(90,15,30,.55) 45%,rgba(20,5,10,.85) 100%)}
  .intro{left:22px;top:32px;width:285px;font-size:8.2px;line-height:1.42;font-weight:500}
  .col-heading{font-size:13.5px;font-weight:500;line-height:1.15;margin-bottom:3px}
  .col-text{font-size:7.8px;line-height:1.45;font-weight:500}
  .included{left:22px;top:80px;width:140px}
  .about{left:173px;top:80px;width:135px}
  .portrait-lg{left:22px;top:163px;width:131px;height:131px;background:linear-gradient(135deg,#d9cbbf,#b99c86 60%,#8a6a55)}
  .for-me{left:173px;top:160px;width:135px}
  .brand-chip{left:22px;top:405px;width:81px;height:28px;background:var(--paper);display:flex;align-items:center;gap:3px;padding:0 5px}
  .brand-chip .dot{width:6px;height:6px;border-radius:50%;background:var(--rose);flex:none}
  .brand-chip span{font-size:7px;font-weight:600;color:var(--rose);white-space:nowrap}
  .contact{left:134px;top:398px;font-size:11.5px;line-height:1.5;font-weight:500}

  /* cover panel */
  .panel--cover{background:linear-gradient(180deg,var(--paper) 0%,var(--mist) 100%);color:var(--ink)}
  .cover-brand{left:0;right:0;top:28px;display:flex;align-items:center;justify-content:center;gap:8px}
  .cover-brand .dot{width:16px;height:16px;border-radius:50%;background:var(--rose)}
  .cover-brand span{font-size:21px;font-weight:600;color:var(--rose);letter-spacing:.2px}
  .cover-sub{left:0;right:0;top:58px;text-align:center;font-size:8px;letter-spacing:1.6px;color:#555;font-weight:500}
  .hero-photo{left:74px;top:110px;width:180px;height:180px;border-radius:50%;background:radial-gradient(circle at 45% 40%,#e8b48a,#a86a45 55%,#3a2a30)}
  .ring{left:62px;top:98px;width:204px;height:204px;border-radius:50%;border:8px solid var(--rose)}
  .cover-title{left:0;right:0;top:372px;text-align:center;font-size:15.5px;font-weight:500;color:var(--rose)}
  .cover-byline{left:0;right:0;top:391px;text-align:center;font-size:9.5px;font-weight:500}
  .cover-byline em{font-style:normal;color:var(--rose)}
  .cover-url{left:82px;top:410px;width:164px;height:17px;background:var(--rose);color:var(--paper);font-family:"Montserrat",sans-serif;font-size:7px;font-weight:600;display:flex;align-items:center;justify-content:center}

  /* testimonials */
  .panel--voices-a{background:linear-gradient(180deg,var(--rose-deep) 0%,var(--rose) 50%,#b23350 100%)}
  .panel--voices-b{background:linear-gradient(180deg,var(--charcoal) 0%,var(--charcoal-deep) 100%)}
  .testimonial{left:22px;width:285px;display:flex;gap:10px}
  .testimonial .photo{width:73px;height:73px;flex:none;background:linear-gradient(160deg,#e6d4c6,#b99783 60%,#6f574c)}
  .testimonial h3{font-size:11.5px;font-weight:500;line-height:1.15;margin-bottom:2px}
  .testimonial p{font-family:"Montserrat",sans-serif;font-size:4.6px;font-weight:600;line-height:1.5}
  .t1{top:30px}.t2{top:137px}.t3{top:252px}.t4{top:359px}
  .learn{left:22px;top:236px;width:290px}
  .learn h3{font-size:12.5px;font-weight:500;margin-bottom:3px}
  .learn ul{display:grid;grid-template-columns:1fr 1fr;column-gap:14px;list-style:none}
  .learn li{font-size:7.2px;line-height:1.45;padding-left:8px;position:relative;margin-bottom:2px}
  .learn li::before{content:"";position:absolute;left:0;top:3px;width:3.5px;height:3.5px;border-radius:50%;background:var(--paper)}
  .cta{left:22px;top:317px;font-size:22px;font-weight:600;line-height:.95;text-transform:uppercase}
  .price{left:182px;top:317px;font-size:22px;font-weight:600;line-height:.95;text-transform:uppercase}
  .register{left:0;right:0;top:382px;text-align:center;font-size:12px;font-weight:500}
  .fineprint{left:0;right:0;top:399px;text-align:center;font-size:5.4px;line-height:1.5;font-weight:500}
  .cancel{left:0;right:0;top:438px;text-align:center;font-size:8.6px;font-weight:500}
</style>
</head>
<body>

<section class="spread spread--outer">
  <div class="panel panel--back">
    <div class="abs crowd-photo" role="img" aria-label="Photo of women gathered at a seminar, tinted red"></div>
    <p class="abs intro">Immerse yourself with a group of likeminded individuals in a weekly masterclass and get absorbed in some of the most senior relationships content that's changing the lives of thousands of women internationally.</p>
    <div class="abs included">
      <h2 class="col-heading">What's Included:</h2>
      <p class="col-text">1. Receive full access to the Masterclasses Series Programme (once a week)<br>2. Gain full access to the network via our private members' online group.</p>
    </div>
    <div class="abs about">
      <h2 class="col-heading">About The Masterclass:</h2>
      <p class="col-text">Immerse yourself for one hour a week with like-minded individuals from the comfort and safety of your own home. Mondays 7pm-8pm</p>
    </div>
    <div class="abs portrait-lg" role="img" aria-label="Portrait photo of the programme host"></div>
    <div class="abs for-me">
      <h2 class="col-heading" style="font-size:15px">Is this programme for me?</h2>
      <p class="col-text">If you wish to Join one of the UK's Top Female Networks for a Life Changing Year but the unlimited programme is out of budget, then the Masterclass programme is for you. Give yourself that step in between, The Masterclass Programme Series. We've packaged it up so that you can afford it!</p>
    </div>
    <div class="abs brand-chip"><i class="dot"></i><span>HEARTWAYS COLLECTIVE</span></div>
    <p class="abs contact">+44 20 7946 0321<br>contact@heartwayscollective.example</p>
  </div>

  <div class="panel panel--cover">
    <div class="abs cover-brand"><i class="dot"></i><span>HEARTWAYS COLLECTIVE</span></div>
    <p class="abs cover-sub">BONDING SKILLS PROGRAMME</p>
    <div class="abs ring"></div>
    <div class="abs hero-photo" role="img" aria-label="Photo of the host smiling and celebrating"></div>
    <h1 class="abs cover-title">Uk's #1 Relationship Seminar For Women Only</h1>
    <p class="abs cover-byline">With Clara Whitmore: #1 Best-selling Author of "<em>Rise And Bloom</em>"</p>
    <p class="abs cover-url">www.heartwayscollective.example</p>
  </div>
</section>

<section class="spread spread--inner">
  <div class="panel panel--voices-a">
    <article class="abs testimonial t1">
      <div class="photo" role="img" aria-label="Portrait photo of Leila Harmon"></div>
      <div><h3>Leila Harmon, 34, Missing and exploitation coordinator</h3>
      <p>I joined to solve issues I had in my relationships with men that I had been carrying for a long time. Through this work I can now see things from a new angle. The old conversation in my mind is gone and I feel free now. A truly life changing experience for which I am grateful.</p></div>
    </article>
    <article class="abs testimonial t2">
      <div class="photo" role="img" aria-label="Portrait photo of Janet Morley"></div>
      <div><h3>Janet Morley, 63, Midwife Labour Ward</h3>
      <p>"I honestly didn't know how this would help me through the pain of my marriage breakup. Then one evening something in the message landed. I kept joining the classes, applied the tools each day and slowly found space to breathe. A few weeks later I felt a real shift, a sense of peace, and I could manage these huge emotions. I've loved every minute of it."</p></div>
    </article>
    <article class="abs testimonial t3">
      <div class="photo" role="img" aria-label="Portrait photo of Sofia Brandt"></div>
      <div><h3>Sofia Brandt, 39, Receptionist for Adult Mental Health</h3>
      <p>I feel so lucky to have found this group of amazing women. The series has opened my eyes to how I treat myself, my thoughts and my mindset. It has given me in depth tools to break old cycles, and I have learnt to give myself more compassion and self-love.</p></div>
    </article>
    <article class="abs testimonial t4">
      <div class="photo" role="img" aria-label="Portrait photo of Tamsin"></div>
      <div><h3>Tamsin, 42, Hairstylist</h3>
      <p>The masterclasses are a great way to keep the teaching alive in my mind after the weekends. The questions and answers show me practical ways others use the tools, and I gain insight into my own habits and thinking. I value the courage and wisdom of the other members.</p></div>
    </article>
  </div>

  <div class="panel panel--voices-b">
    <article class="abs testimonial t1">
      <div class="photo" role="img" aria-label="Portrait photo of Harriet Vale"></div>
      <div><h3>Harriet Vale, 33, Senior Customer Success Manager</h3>
      <p>Masterclasses are like mini mastery weekends, truly life changing. I finally see why I kept reliving old patterns of comparison and feeling not good enough. I now have the tools to notice these emotions as they arise and process them. I'm finally ready to love and accept myself for who I am.</p></div>
    </article>
    <article class="abs testimonial t2">
      <div class="photo" role="img" aria-label="Portrait photo of Marisol Ortega"></div>
      <div><h3>Marisol Ortega, 38, Director of Luxury Sales</h3>
      <p>The series is my most important weekly date with myself! It offers a deeper learning of all the tools, the chance to go through each one in detail and practise them daily. Hearing how senior members use the tools to feel safer within themselves is so powerful.</p></div>
    </article>
    <div class="abs learn">
      <h3>What will I learn/ get from the programme?</h3>
      <ul>
        <li>Weekly opportunity to have all your burning relationship questions answered</li>
        <li>Tools to help you overcome past relationship wounds and patterns</li>
        <li>Immerse with a powerful network of like-minded women and learn even more</li>
        <li>Deepen your understanding of self-mastery on route to relationship Mastery</li>
      </ul>
    </div>
    <p class="abs cta">Don't let today<br><span style="font-size:28px">finish here.</span></p>
    <p class="abs price">Subscription:<br><span style="font-size:25px">£200 a month</span></p>
    <p class="abs register">Register today and get the first months' worth TODAY.</p>
    <p class="abs fineprint">Tomorrow, wake up and watch half a day of the most powerful content for relationships out there.<br>That's half a day of advanced content for only £200.</p>
    <p class="abs cancel">If at any point you wish to cancel your subscription, just give us 30 days notice.</p>
  </div>
</section>

</body>
</html>
```